Fern Acupuncture Business Card Design

I would like a business card design for my acupuncture business which is based from 2 practices in Melbourne, Australia.

The front of the card should include:

*The Logo
* Name - Miranda Tesselhoff (B.App.Sc.(TCM), Dip.Rem.Mass.). (I would like the letters after my name in slightly smaller font)
* Mobile number - 0472 318 604
* Web address - www.fernacupuncture.com.au

On the back of the card I would somehow like to fit my 2 clinic addresses in. They are:

The Calm & Balance Rooms
842 Pellam St, Camberwell VIC 3124
Ph: 1300 287 419

Riverbend Natural Therapies & Herbal Practice
19 Quillon Ave, Malvern East VIC 3145
Ph: (03) 9731 4052

If there is space, I'd also like to add to the back of the card - Next Appointment............................ (or something along those lines).

Thanks and happy designing!

Target Market(s)

Health consumers, and colleagues in the health industry

Industry/Entity Type

Clinic

Contact Information for Business Card

as above in brief

Requirements
Must have
• I've seen some ok designs coming in, however I'd like to avoid the generic look with the added curved line details etc. I don't particularly need extra patterns added to the card. I'd prefer it to look quite clean and simple, and using more earthy colours (I'm not super keen on the lime green that a lot of designs seem to include. I don't mind the full black or white look, (obviously the back side needs to be a lighter colour to allow me to write appointment details on it). I also quite like the idea of the background looking like brown recycled paper (just an idea - that's not 100% necessary).
Nice to have
• I have an idea that I could have the main flower part of the logo printed as metallic.
Should not have
• Generic patterns and too much added detail.

```html
<!DOCTYPE html>
<html lang="en">
<head>
<meta charset="utf-8">
<title>Fern Acupuncture – Business Card</title>
<link rel="stylesheet" href="https://fonts.googleapis.com/css2?family=Cinzel:wght@600&family=Arimo:wght@400;700&display=swap">
<style>
  :root {
    --kraft: #a9835a;
    --kraft-deep: #8c6a45;
    --paper: #efe6d4;
    --ink: #1c1610;
    --cream: #f6efdc;
    --muted: #5b4a38;
    --backdrop: #e9e4da;
  }
  * { box-sizing: border-box; margin: 0; padding: 0; }
  html, body { width: 1200px; height: 800px; overflow: hidden; }
  body { background: var(--backdrop); position: relative; font-family: "Arimo", Arial, sans-serif; }

  .card {
    position: absolute;
    width: 520px;
    height: 300px;
    overflow: hidden;
    box-shadow: 0 6px 18px rgba(0,0,0,0.18);
  }
  .card--front { left: 50px; top: 120px; background: var(--kraft); }
  .card--back  { left: 630px; top: 380px; background: var(--paper); }

  /* Front */
  .base-band { position: absolute; left: 0; bottom: 0; width: 100%; height: 44px; background: var(--ink); }

  .brand {
    position: absolute; left: 0; top: 0; width: 205px; height: 256px;
    display: flex; flex-direction: column; align-items: center; justify-content: center; gap: 14px;
  }
  .brand__dot { width: 96px; height: 96px; border-radius: 50%; background: var(--ink); }
  .brand__name { font-family: "Cinzel", Georgia, serif; font-weight: 600; font-size: 15px; color: var(--ink); letter-spacing: 0.5px; }
  .divider { position: absolute; left: 205px; top: 28px; width: 2px; height: 200px; background: var(--ink); }

  .practitioner { position: absolute; left: 232px; top: 40px; }
  .practitioner__name { font-family: "Cinzel", Georgia, serif; font-weight: 600; font-size: 22px; color: var(--ink); letter-spacing: 0.5px; }
  .practitioner__quals { font-size: 10.5px; color: var(--cream); margin-top: 6px; }

  .contacts { position: absolute; left: 232px; top: 132px; color: var(--cream); font-size: 15px; line-height: 1; }
  .contacts p + p { margin-top: 18px; }

  /* Back */
  .clinic { position: absolute; left: 30px; color: var(--muted); font-size: 13px; line-height: 1.4; }
  .clinic--one { top: 28px; }
  .clinic--two { top: 108px; }
  .clinic__name { color: var(--ink); font-size: 14.5px; font-weight: 700; }
  .clinic__phone { display: flex; align-items: center; gap: 8px; margin-top: 2px; }
  .clinic__phone svg { width: 13px; height: 13px; fill: var(--ink); }

  .appointment {
    position: absolute; left: 0; bottom: 0; width: 100%; height: 82px;
    background: var(--kraft); padding: 0 30px;
    display: flex; align-items: center; gap: 14px;
  }
  .appointment__label { color: var(--ink); font-size: 15px; font-weight: 700; white-space: nowrap; }
  .appointment__lines { flex: 1; display: flex; flex-direction: column; gap: 18px; padding-top: 14px; }
  .appointment__line { display: block; border-top: 2px dotted var(--ink); }
</style>
</head>
<body>

  <section class="card card--front" aria-label="Card front">
    <div class="brand">
      <span class="brand__dot"></span>
      <span class="brand__name">Fern Acupuncture</span>
    </div>
    <span class="divider"></span>
    <div class="practitioner">
      <h1 class="practitioner__name">Miranda Tesselhoff</h1>
      <p class="practitioner__quals">B.App.Sc.(TCM), Dip.Rem.Mass.</p>
    </div>
    <div class="contacts">
      <p>0472 318 604</p>
      <p>www.fernacupuncture.com.au</p>
    </div>
    <span class="base-band"></span>
  </section>

  <section class="card card--back" aria-label="Card back">
    <div class="clinic clinic--one">
      <h2 class="clinic__name">The Calm &amp; Balance Rooms</h2>
      <p>842 Pellam St, Camberwell VIC 3124</p>
      <p class="clinic__phone">
        <svg viewBox="0 0 24 24" aria-hidden="true"><path d="M6.6 10.8a15.1 15.1 0 0 0 6.6 6.6l2.2-2.2a1 1 0 0 1 1-.25 11.4 11.4 0 0 0 3.6.57 1 1 0 0 1 1 1V20a1 1 0 0 1-1 1A17 17 0 0 1 3 4a1 1 0 0 1 1-1h3.5a1 1 0 0 1 1 1c0 1.25.2 2.45.57 3.57a1 1 0 0 1-.25 1z"/></svg>
        1300 287 419
      </p>
    </div>

    <div class="clinic clinic--two">
      <h2 class="clinic__name">Riverbend Natural Therapies &amp; Herbal Practice</h2>
      <p>19 Quillon Ave, Malvern East VIC 3145</p>
      <p class="clinic__phone">
        <svg viewBox="0 0 24 24" aria-hidden="true"><path d="M6.6 10.8a15.1 15.1 0 0 0 6.6 6.6l2.2-2.2a1 1 0 0 1 1-.25 11.4 11.4 0 0 0 3.6.57 1 1 0 0 1 1 1V20a1 1 0 0 1-1 1A17 17 0 0 1 3 4a1 1 0 0 1 1-1h3.5a1 1 0 0 1 1 1c0 1.25.2 2.45.57 3.57a1 1 0 0 1-.25 1z"/></svg>
        (03) 9731 4052
      </p>
    </div>

    <div class="appointment">
      <span class="appointment__label">Next Appointment :-</span>
      <span class="appointment__lines">
        <span class="appointment__line"></span>
        <span class="appointment__line"></span>
      </span>
    </div>
  </section>

</body>
</html>
```